Accountancy firm needs clean and simple website and optional logo

We need a logo and basic wordpress website design for a Sydney based accountancy firm.
We need a clean and simple logo and website, based on the accounting/finance/tax industry. Simple, credible and official colors.
The logo is expected to be so simple that we have combined into the one job.
If you submit a logo design and we choose it along with someone else's website design you will be paid a bonus of $60. The website design will still win the competition as per normal.
Current website is old and terrible but gives you an idea of the sitemap (super simple) and what they do: www.brookfiscal.com.au
We want original different to normal template looking designs.
We like videos, and like http://www.merivane.com.au/
Feel free to go to clipvault9 and use some videos from there.
We are based in Sydney Australia and in the field of taxation and accounting
We want a clean, formal, credible site, limited pages.
The project is guaranteed, so go for it.
Logo Text
Brook & Associates

```html
<!DOCTYPE html>
<html lang="en">
<head>
<meta charset="utf-8">
<title>Brook &amp; Associates – Tax Accountants</title>
<link href="https://fonts.googleapis.com/css2?family=Questrial&family=Open+Sans:wght@400;600;700&display=swap" rel="stylesheet">
<style>
:root{
  --blue:#0b8ee0;
  --blue-dark:#0a7fcc;
  --ink:#1b1b1b;
  --text:#555;
  --grey-band:#f0f0f0;
  --footer:#222;
  --line:#ddd;
  --white:#fff;
}
*{margin:0;padding:0;box-sizing:border-box}
html,body{width:751px;height:1200px;overflow:hidden;background:var(--white)}
body{position:relative;font-family:'Open Sans',sans-serif;color:var(--text)}
.abs{position:absolute}
.heading{font-family:'Questrial',sans-serif;color:var(--ink);text-transform:uppercase}

/* header */
.brand{left:50px;top:36px;display:flex;align-items:center;gap:8px}
.brand-mark{width:14px;height:14px;background:var(--blue)}
.brand-name{font-family:'Questrial',sans-serif;font-size:11px;color:var(--ink);line-height:1.15}
.contact-top{left:543px;top:20px;display:flex;align-items:center;gap:12px}
.phone-box{width:30px;height:30px;border:1.5px solid var(--ink);display:flex;align-items:center;justify-content:center}
.contact-top .tel{font-family:'Questrial',sans-serif;font-size:13px;color:var(--ink);line-height:1.1}
.contact-top .mail{font-size:8.5px;color:var(--ink)}

/* nav */
.nav{left:0;top:70px;width:751px;height:31px;background:var(--blue);box-shadow:0 2px 3px rgba(0,0,0,.15)}
.nav ul{list-style:none;display:flex;margin-left:50px;width:651px;border-left:1px solid rgba(255,255,255,.25)}
.nav li{width:108.5px;height:31px;line-height:31px;text-align:center;color:#fff;font-size:8.5px;font-family:'Questrial',sans-serif;border-right:1px solid rgba(255,255,255,.25)}

/* hero */
.hero{left:0;top:101px;width:751px;height:381px;background:linear-gradient(180deg,#a9cfd0 0%,#cfe3df 45%,#8cb4c1 62%,#d9cdb8 76%,#9a6e5c 88%,#6f4e44 100%)}
.hero-title{left:402px;top:240px;font-family:'Questrial',sans-serif;line-height:1}
.hero-title .l1{font-size:37px;color:var(--blue)}
.hero-title .l2{font-size:25px;color:var(--ink);margin-top:4px}
.dots{left:337px;top:460px;display:flex;gap:10px}
.dots span{width:7px;height:7px;border-radius:50%;background:#fff}
.dots span.on{background:var(--blue)}

/* services */
.card{top:504px;width:207px;height:264px;border:1px solid var(--line);box-shadow:0 1px 2px rgba(0,0,0,.06);text-align:center}
.card .photo{margin:5px auto 0;width:193px;height:110px}
.card h3{font-size:12.5px;margin-top:19px;font-weight:400}
.card p{font-size:7.3px;line-height:14px;margin:12px 12px 0;height:44px}
.btn{display:inline-block;background:var(--blue);color:#fff;font-family:'Questrial',sans-serif;font-size:8.5px;width:79px;height:28px;line-height:28px;text-align:center}
.card .btn{margin-top:11px}

/* about / why */
.section-title{font-size:12.5px;font-weight:400}
.about-text{left:51px;top:855px;width:310px;font-size:7.3px;line-height:15.2px}
.why-item{left:390px;display:flex;gap:18px}
.why-item .ico{width:26px;height:24px}
.why-item h4{font-family:'Questrial',sans-serif;color:var(--blue);font-size:11.5px;font-weight:400}
.why-item p{font-size:7.3px;margin-top:5px}

/* disclaimer */
.disclaimer{left:0;top:1017px;width:751px;height:96px;background:var(--grey-band);padding:24px 52px}
.disclaimer h5{font-size:9.5px;font-weight:400}
.disclaimer p{font-size:7.3px;line-height:15px;margin-top:6px}

/* contact bar */
.contact-bar{left:0;top:1113px;width:751px;height:46px;background:var(--blue);color:#fff;font-size:7.3px;font-weight:600}
.contact-bar .item{position:absolute;top:17px;display:flex;align-items:center;gap:7px}

/* footer */
.footer{left:0;top:1159px;width:751px;height:41px;background:var(--footer);color:#fff;font-size:7.5px}
.footer .copy{position:absolute;left:50px;top:15px}
.footer .follow{position:absolute;left:546px;top:14px;display:flex;align-items:center;gap:10px}
.footer .follow i{width:8px;height:8px;border-radius:50%;background:var(--blue);display:block}
</style>
</head>
<body>

<header>
  <div class="abs brand">
    <span class="brand-mark"></span>
    <div class="brand-name">BROOK &amp; ASSOCIATES<br><span style="font-size:8px">tax accountants</span></div>
  </div>
  <div class="abs contact-top">
    <div class="phone-box">
      <svg width="12" height="12" viewBox="0 0 24 24"><path fill="#0b8ee0" d="M6.6 10.8a15.1 15.1 0 0 0 6.6 6.6l2.2-2.2a1 1 0 0 1 1-.25 11.4 11.4 0 0 0 3.6.57 1 1 0 0 1 1 1V20a1 1 0 0 1-1 1A17 17 0 0 1 3 4a1 1 0 0 1 1-1h3.5a1 1 0 0 1 1 1c0 1.25.2 2.45.57 3.57a1 1 0 0 1-.25 1z"/></svg>
    </div>
    <div>
      <div class="tel">+61 (2) 9000 4821</div>
      <div class="mail">support@brookfiscal.com.au</div>
    </div>
  </div>
</header>

<nav class="abs nav">
  <ul><li>HOME</li><li>ABOUT US</li><li>SERVICES</li><li>TESTIMONIALS</li><li>OUR TEAM</li><li>CONTACT US</li></ul>
</nav>

<section class="abs hero" role="img" aria-label="Photo: man working on a laptop in a deck chair on a boardwalk by the beach">
</section>
<div class="abs hero-title">
  <div class="l1">Take the Worry</div>
  <div class="l2">Out of Tax and Business</div>
</div>
<div class="abs dots"><span></span><span></span><span class="on"></span><span></span><span></span></div>

<section class="services">
  <article class="abs card" style="left:49px">
    <div class="photo" role="img" aria-label="Photo: business people in a meeting with a tablet" style="background:linear-gradient(135deg,#2c3e5c,#9fb0c6 55%,#e8ecf0)"></div>
    <h3 class="heading">Tax Planning</h3>
    <p>In over 14 countries world wide and with over 200 employees we truly cover all aspects of your business, let us bring you back the joy.</p>
    <span class="btn">READ MORE</span>
  </article>
  <article class="abs card" style="left:272px">
    <div class="photo" role="img" aria-label="Photo: hands reviewing financial charts on paper" style="background:linear-gradient(135deg,#c9d3dc,#f2f4f6 50%,#3a3d44)"></div>
    <h3 class="heading">GST Preparation</h3>
    <p>Let our dedicated staff take care of al your audit services. Paperwork, contracts, legal,... we take care of all the boring things.</p>
    <span class="btn">READ MORE</span>
  </article>
  <article class="abs card" style="left:494px">
    <div class="photo" role="img" aria-label="Photo: business handshake in an office" style="background:linear-gradient(135deg,#e4e8ee,#7d8794 55%,#2e3540)"></div>
    <h3 class="heading">Litigation Assistance</h3>
    <p>We understand the importance of organised tax accounting. We get the most out of it and keep following all the changes.</p>
    <span class="btn">READ MORE</span>
  </article>
</section>

<section class="about">
  <h2 class="abs heading section-title" style="left:51px;top:814px">About Us</h2>
  <p class="abs about-text">We have over 20 years of experience providing expert financial advice for both businesses and individuals. Our Investment Committee brings decades of industry expertise in driving our investment approach, portfolio construction, and allocation advice. The committee ensures our investments are best in class, combining substantiated research with the most effective investing tools available today. Lorem ipsum dolor sit amet, consectetur adipiscing elit. In sit amet tellus diam.</p>
  <span class="abs btn" style="left:50px;top:961px">READ MORE</span>
</section>

<section class="why">
  <h2 class="abs heading section-title" style="left:383px;top:814px">Why Choose Us?</h2>
  <div class="abs why-item" style="top:851px">
    <svg class="ico" viewBox="0 0 26 24"><rect x="1" y="6" width="24" height="16" rx="2" fill="#0b8ee0"/><rect x="9" y="2" width="8" height="5" rx="1" fill="none" stroke="#0b8ee0" stroke-width="2"/><rect x="1" y="12" width="24" height="1.5" fill="#fff"/></svg>
    <div><h4>Experienced</h4><p>We have over 20 years experience providing expert financial advice.</p></div>
  </div>
  <div class="abs why-item" style="top:903px">
    <svg class="ico" viewBox="0 0 26 24"><circle cx="6" cy="8" r="3" fill="#0b8ee0"/><circle cx="20" cy="8" r="3" fill="#0b8ee0"/><circle cx="13" cy="5" r="3.5" fill="#0b8ee0"/><path d="M1 22v-7a3 3 0 0 1 3-3h4a3 3 0 0 1 3 3v7zM15 22v-7a3 3 0 0 1 3-3h4a3 3 0 0 1 3 3v7z" fill="#0b8ee0"/><path d="M8 22v-9a3 3 0 0 1 3-3h4a3 3 0 0 1 3 3v9z" fill="#0b8ee0" stroke="#fff"/></svg>
    <div><h4>Vibrant</h4><p>A young, enthusiastic team of advisors are always here to help.</p></div>
  </div>
  <div class="abs why-item" style="top:957px">
    <svg class="ico" viewBox="0 0 26 24"><circle cx="13" cy="5" r="4.5" fill="#0b8ee0"/><path d="M4 24v-7a6 6 0 0 1 6-6h6a6 6 0 0 1 6 6v7z" fill="#0b8ee0"/></svg>
    <div><h4>Professional</h4><p>Our financial specialists ensure you get the optimum results.</p></div>
  </div>
</section>

<section class="abs disclaimer">
  <h5 class="heading">Disclaimer</h5>
  <p>We do the best we can to keep information up to date on this site. We can, however, make errors, so before making any decisions that will cost you money, you should confirm the details upon which you rely.</p>
</section>

<section class="abs contact-bar">
  <div class="item" style="left:56px">
    <svg width="10" height="10" viewBox="0 0 24 24"><path fill="#fff" d="M6.6 10.8a15.1 15.1 0 0 0 6.6 6.6l2.2-2.2a1 1 0 0 1 1-.25 11.4 11.4 0 0 0 3.6.57 1 1 0 0 1 1 1V20a1 1 0 0 1-1 1A17 17 0 0 1 3 4a1 1 0 0 1 1-1h3.5a1 1 0 0 1 1 1c0 1.25.2 2.45.57 3.57a1 1 0 0 1-.25 1z"/></svg>+61 (2) 9000 4821</div>
  <div class="item" style="left:199px">
    <svg width="10" height="10" viewBox="0 0 10 10"><rect x="0" y="3" width="10" height="7" rx="1" fill="#fff"/><rect x="2" y="0" width="6" height="3" fill="#fff"/></svg>+61 (2) 9000 4822</div>
  <div class="item" style="left:340px">
    <svg width="10" height="8" viewBox="0 0 10 8"><rect width="10" height="8" rx="1" fill="#fff"/><path d="M0 1l5 3.5L10 1" fill="none" stroke="#0b8ee0"/></svg>info@brookfiscal.com.au</div>
  <div class="item" style="left:489px">
    <svg width="8" height="11" viewBox="0 0 8 11"><path d="M4 0a4 4 0 0 1 4 4c0 3-4 7-4 7S0 7 0 4a4 4 0 0 1 4-4z" fill="#fff"/><circle cx="4" cy="4" r="1.5" fill="#0b8ee0"/></svg>Suite 3B, 118 Harbour Row, Eastvale, NSW 2090</div>
</section>

<footer class="abs footer">
  <div class="copy">Brookfiscal © 2015 Copyrights. All Rights Reserved. &nbsp;&nbsp;&nbsp; SiteMap &nbsp; | &nbsp; Privacy Policy</div>
  <div class="follow">Follow Us : <i></i><i></i><i></i><i></i><i></i></div>
</footer>

</body>
</html>
```